Veltra Cosmi Holdings Limited is a asset management company and project funding company, we specialise in high end finance for high net worth individuals, we are looking for a new logo letterhead template, email footer template and business card design. The letterhead template should be designed in word format so that the letterheading can be used electronically.

Below is the current logo that is a but plain and a little cheaper looking, colour schemes are not important just that it looks professional.

I am looking for a sharp impact that stands out,

Target Market(s)

High net worth individuals and institutions

Industry/Entity Type

Finance

Contact Information for Business Card

Veltra Cosmi Holdings Limited
T: 0333 418 2965

M: 07631 490718
E:derek.holm@veltra-cosmiholdings.com

REEDWATER COVE, EAST HARBOUR ROAD
FIFTH FLOOR, SUITE 512
P.O. BOX CB-47316
NASSAU BAHAMAS

Logo Text

Font styles to use
Serif
Sans Serif
Script
Other font styles liked:
• Tahoma

Colors
fbed22
6b449b
ec1f27
f78f20
33b8a4
0592cd

Requirements
Must have
• Colours schemes would look good in blue’s green’s purples.

Yellow and Purple together maybe a nice combination.
Nice to have
• I want the log to look sharpe, relate to a global presence, but I also want to it to look established.
Should not have
• N/a

```html
<!DOCTYPE html>
<html lang="en">
<head>
<meta charset="utf-8">
<title>Veltra Cosmi Holdings Limited – Stationery</title>
<link href="https://fonts.googleapis.com/css2?family=Hind:wght@400;500&family=Poppins:wght@400;500;600;700&display=swap" rel="stylesheet">
<style>
  :root {
    --blue: #0f94dc;
    --green: #74b414;
    --ink: #1f1f1f;
    --paper: #ffffff;
    --card-dark: #0d0d0d;
    --backdrop: #8a8a8a;
    --faint: #f1f1f1;
  }
  * { box-sizing: border-box; margin: 0; padding: 0; }
  html, body { width: 1200px; height: 1054px; overflow: hidden; }
  body { background: var(--backdrop); position: relative; font-family: "Hind", sans-serif; color: var(--ink); }

  .sheet, .card { position: absolute; background: var(--paper); overflow: hidden; }

  /* tri-colour bars */
  .tribar { position: absolute; left: 0; right: 0; height: 16px; display: flex; gap: 5px; }
  .tribar span { display: block; height: 100%; }
  .tribar .b { background: var(--blue); flex: 359; }
  .tribar .g { background: var(--green); flex: 345; }
  .tribar .b2 { background: var(--blue); flex: 360; }

  /* brand name block */
  .brand { position: absolute; text-align: center; font-family: "Poppins", sans-serif; font-weight: 600; color: var(--ink); line-height: 1; }
  .brand .dot { display: block; margin: 0 auto; border-radius: 50%; background: var(--blue); }
  .brand .line1 { display: block; letter-spacing: 0.02em; }
  .brand .line2 { display: block; letter-spacing: 0.04em; }

  /* letterhead */
  .letterhead { left: 42px; top: 56px; width: 637px; height: 902px; }
  .letterhead .tribar { top: 0; }
  .letterhead .brand { left: 58px; top: 42px; width: 200px; }
  .letterhead .brand .dot { width: 52px; height: 52px; margin-bottom: 10px; }
  .letterhead .brand .line1 { font-size: 27px; }
  .letterhead .brand .line2 { font-size: 17px; margin-top: 5px; }
  .lh-address { position: absolute; left: 430px; top: 40px; font-family: "Poppins", sans-serif; font-size: 9.4px; line-height: 12px; text-transform: uppercase; }
  .lh-address svg { position: absolute; left: -20px; top: 0; }
  .lh-recipient { position: absolute; left: 59px; font-size: 14px; }
  .lh-date { position: absolute; right: 60px; top: 234px; font-size: 14px; }
  .lh-body { position: absolute; left: 59px; top: 277px; width: 518px; font-size: 13.9px; line-height: 16.5px; text-align: justify; }
  .lh-body p + p { margin-top: 16.5px; }
  .signature { position: absolute; left: 40px; top: 669px; width: 150px; height: 62px; background: linear-gradient(90deg, #eeeeee, #f7f7f7); }
  .lh-signoff { position: absolute; left: 59px; font-size: 14px; line-height: 16.5px; }
  .lh-footer { position: absolute; left: 0; bottom: 0; width: 637px; height: 75px; }

  /* business cards */
  .card-dark { left: 714px; top: 118px; width: 441px; height: 251px; background: var(--card-dark); }
  .card-dark .brand { left: 0; right: 0; top: 50px; color: #ffffff; }
  .card-dark .brand .dot { width: 68px; height: 68px; margin-bottom: 20px; }
  .card-dark .brand .line1 { font-size: 38px; }
  .card-dark .brand .line2 { font-size: 25px; margin-top: 6px; }
  .card .tribar { bottom: 0; height: 10px; gap: 4px; }

  .card-contact { left: 714px; top: 421px; width: 441px; height: 252px; }
  .faint-mark { position: absolute; left: 268px; top: 67px; width: 210px; height: 210px; border-radius: 50%; background: var(--faint); }
  .cc-name { position: absolute; left: 40px; top: 33px; font-family: "Poppins", sans-serif; font-weight: 700; font-size: 27px; line-height: 33px; text-transform: uppercase; }
  .cc-name .top { color: var(--blue); display: block; }
  .cc-name .bottom { color: var(--green); display: block; }
  .cc-details { position: absolute; left: 14px; top: 108px; font-family: "Poppins", sans-serif; font-size: 12.4px; color: var(--ink); }
  .cc-row { position: relative; padding-left: 26px; line-height: 15px; margin-bottom: 7px; }
  .cc-row svg { position: absolute; left: 0; top: 0; }
  .cc-row.address { text-transform: uppercase; }

  .card-logo { left: 714px; top: 741px; width: 486px; height: 217px; }
  .card-logo .brand { left: 0; width: 472px; top: 14px; }
  .card-logo .brand .dot { width: 86px; height: 86px; margin-bottom: 20px; }
  .card-logo .brand .line1 { font-size: 50px; }
  .card-logo .brand .line2 { font-size: 32px; margin-top: 6px; }
</style>
</head>
<body>

<!-- Letterhead -->
<section class="sheet letterhead">
  <div class="tribar"><span class="b"></span><span class="g"></span><span class="b2"></span></div>

  <div class="brand">
    <span class="dot"></span>
    <span class="line1">VELTRA COSMI</span>
    <span class="line2">HOLDINGS LIMITED</span>
  </div>

  <address class="lh-address" style="font-style:normal">
    <svg width="15" height="15" viewBox="0 0 16 16" aria-hidden="true"><circle cx="8" cy="8" r="8" fill="var(--blue)"/><path d="M8 3.2a3 3 0 0 0-3 3c0 2.2 3 5.8 3 5.8s3-3.6 3-5.8a3 3 0 0 0-3-3z" fill="#fff"/><circle cx="8" cy="6.2" r="1.1" fill="var(--blue)"/></svg>
    Reedwater Cove, East Harbour Road<br>
    Fifth Floor, Suite 512<br>
    P.O. Box CB-47316<br>
    Nassau Bahamas
  </address>

  <p class="lh-recipient" style="top:201px">Your Name Here</p>
  <p class="lh-recipient" style="top:234px">Address</p>
  <p class="lh-date">Date : 17th September, 2020</p>

  <div class="lh-body">
    <p>Lorem Ipsum is simply dummy text of the printing and typesetting industry. Lorem Ipsum has been the industry's standard dummy text ever since the 1500s, when an unknown printer took a galley of type and scrambled it to make a type specimen book. It has survived not only five centuries, but also the leap into electronic typesetting, remaining essentially unchanged. It was popularised in the 1960s with the release of Letraset sheets containing Lorem Ipsum passages, and more recently with desktop publishing software like Aldus PageMaker including versions of Lorem Ipsum.</p>
    <p>Lorem Ipsum is simply dummy text of the printing and typesetting industry. Lorem Ipsum has been the industry's standard dummy text ever since the 1500s, when an unknown printer took a galley of type and scrambled it to make a type specimen book. but also the leap into electronic typesetting, remaining essentially unchanged. It was popularised in the 1960s with the release of Letraset sheets containing Lorem Ipsum passages, and more recently with desktop publishing software like Aldus PageMaker including versions of Lorem Ipsum.</p>
    <p>It has survived not only five centuries, but also the leap into electronic typesetting, remaining essentially unchanged. It was popularised in the 1960s with the release of Letraset sheets containing Lorem Ipsum passages, and more recently with desktop publishing software like Aldus PageMaker including versions of Lorem Ipsum.</p>
  </div>

  <p class="lh-signoff" style="top:641px">Regards,</p>
  <div class="signature" role="img" aria-label="Handwritten signature of the sender"></div>
  <p class="lh-signoff" style="top:748px">Your Name Here<br>Designation Here</p>

  <svg class="lh-footer" viewBox="0 0 637 75" aria-hidden="true">
    <rect x="0" y="0" width="637" height="4" fill="var(--blue)"/>
    <rect x="0" y="4" width="637" height="71" fill="var(--blue)"/>
    <polygon points="310,12 637,12 637,75 262,75" fill="#fff"/>
    <polygon points="323,12 637,12 637,75 276,75" fill="var(--green)"/>
    <polygon points="300,4 637,4 637,12 294,12" fill="var(--blue)"/>
    <circle cx="75" cy="42" r="15" fill="#fff"/>
    <rect x="70" y="33" width="10" height="18" rx="2" fill="none" stroke="var(--blue)" stroke-width="1.6"/>
    <text x="103" y="50" font-family="Poppins, sans-serif" font-size="20" fill="#fff">0333 418 2965</text>
    <text x="577" y="50" text-anchor="end" font-family="Poppins, sans-serif" font-size="19" fill="#fff">Company No. 284713C</text>
  </svg>
</section>

<!-- Business card: dark front -->
<section class="card card-dark">
  <div class="brand">
    <span class="dot"></span>
    <span class="line1">VELTRA COSMI</span>
    <span class="line2">HOLDINGS LIMITED</span>
  </div>
  <div class="tribar"><span class="b"></span><span class="g"></span><span class="b2"></span></div>
</section>

<!-- Business card: contact side -->
<section class="card card-contact">
  <div class="faint-mark"></div>
  <h2 class="cc-name"><span class="top">Veltra Cosmi</span><span class="bottom">Holdings Limited</span></h2>
  <div class="cc-details">
    <div class="cc-row">
      <svg width="15" height="15" viewBox="0 0 16 16" aria-hidden="true"><circle cx="8" cy="8" r="8" fill="var(--blue)"/><rect x="5.5" y="3.5" width="5" height="9" rx="1" fill="none" stroke="#fff" stroke-width="1.2"/></svg>
      0333 418 2965 / &nbsp;07631 490718
    </div>
    <div class="cc-row">
      <svg width="15" height="15" viewBox="0 0 16 16" aria-hidden="true"><circle cx="8" cy="8" r="8" fill="var(--blue)"/><rect x="4" y="5" width="8" height="6" fill="none" stroke="#fff" stroke-width="1.2"/><path d="M4 5l4 3.4L12 5" fill="none" stroke="#fff" stroke-width="1.2"/></svg>
      derek.holm@veltra-cosmiholdings.com
    </div>
    <div class="cc-row address">
      <svg width="15" height="15" viewBox="0 0 16 16" aria-hidden="true"><circle cx="8" cy="8" r="8" fill="var(--blue)"/><path d="M8 3.2a3 3 0 0 0-3 3c0 2.2 3 5.8 3 5.8s3-3.6 3-5.8a3 3 0 0 0-3-3z" fill="#fff"/><circle cx="8" cy="6.2" r="1.1" fill="var(--blue)"/></svg>
      Reedwater Cove, East Harbour Road<br>
      Fifth Floor, Suite 512<br>
      P.O. Box CB-47316<br>
      Nassau Bahamas
    </div>
  </div>
  <div class="tribar"><span class="b"></span><span class="g"></span><span class="b2"></span></div>
</section>

<!-- Logo panel -->
<section class="card card-logo">
  <div class="brand">
    <span class="dot"></span>
    <span class="line1">VELTRA COSMI</span>
    <span class="line2">HOLDINGS LIMITED</span>
  </div>
</section>

</body>
</html>
```